Road Construction Company needs business cards

We would like a new business card designed for our business.

We're a road construction company based in Qld, Australia.

Can the business card please have the following information on it.

Name: Warren Halbeck
Position: General Manager
Phone: 0472 915 348
Email: Warren.halbeck@tovrin.com.au
Address: 87 Marrow Ave, Pendlebay, QLD, 4023
Website: www.tovrin.com.au

Visually we'd like the card to be professional and simple.

Attached is our logo.

Our website is www.tovrin.com.au

Target Market(s)

Men aged 25-60

Contact Information for Business Card

As listed in project description

Font styles to use
Serif

Requirements
Must have
• Large logo on back of card

```html
<!DOCTYPE html>
<html lang="en">
<head>
<meta charset="utf-8">
<title>Tovrin Road Construction – Business Cards</title>
<link rel="stylesheet" href="https://fonts.googleapis.com/css2?family=Open+Sans:wght@400;600;700&display=swap">
<style>
  :root {
    --navy: #1458a8;
    --sky: #45abdc;
    --ink: #1b1b1b;
    --paper: #ffffff;
    --backdrop: #1f2024;
  }
  * { box-sizing: border-box; margin: 0; padding: 0; }
  html, body {
    width: 1200px; height: 780px; overflow: hidden;
    background: var(--backdrop);
    font-family: "Open Sans", Arial, sans-serif;
  }
  .sheet {
    position: relative; width: 1200px; height: 780px;
    display: flex; align-items: center; justify-content: center; gap: 40px;
  }
  .card {
    position: relative; width: 540px; height: 310px;
    background: var(--paper);
    border-radius: 18px;
    border-bottom: 4px solid var(--sky);
    overflow: hidden;
  }
  /* Back of card */
  .card-back { display: flex; align-items: center; justify-content: center; }
  .wordmark-large {
    color: var(--navy); font-weight: 700; text-align: center; line-height: 1.05;
  }
  .wordmark-large .name { display: block; font-size: 74px; letter-spacing: 2px; }
  .wordmark-large .descriptor { display: block; font-size: 22px; letter-spacing: 9px; text-transform: uppercase; }

  /* Front of card */
  .swoosh { position: absolute; inset: 0; width: 540px; height: 310px; }
  .corner-tab {
    position: absolute; top: 0; right: 26px; width: 18px; height: 48px; background: var(--navy);
  }
  .holder { position: absolute; top: 22px; right: 56px; text-align: right; }
  .holder-name { color: var(--navy); font-size: 25px; font-weight: 700; line-height: 1.1; }
  .holder-role { color: var(--ink); font-size: 13px; font-weight: 400; }

  .wordmark-small {
    position: absolute; top: 74px; left: 30px;
    color: var(--navy); font-weight: 700; line-height: 1.05;
  }
  .wordmark-small .name { display: block; font-size: 40px; letter-spacing: 1px; }
  .wordmark-small .descriptor { display: block; font-size: 11.5px; letter-spacing: 4.6px; text-transform: uppercase; }

  .address {
    position: absolute; top: 168px; left: 30px;
    color: var(--ink); font-size: 13px; line-height: 1.35;
  }
  .contacts { position: absolute; top: 216px; left: 30px; list-style: none; }
  .contacts li {
    display: flex; align-items: center; gap: 8px;
    color: var(--ink); font-size: 13px; line-height: 1.5;
  }
  .contacts svg { width: 13px; height: 13px; flex: none; }
</style>
</head>
<body>
<main class="sheet">

  <section class="card card-back" aria-label="Back of business card">
    <p class="wordmark-large">
      <span class="name">TOVRIN</span>
      <span class="descriptor">Road Construction</span>
    </p>
  </section>

  <section class="card card-front" aria-label="Front of business card">
    <svg class="swoosh" viewBox="0 0 540 310" aria-hidden="true">
      <path d="M150 310 C 330 300 450 220 540 70 L540 310 Z" fill="var(--navy)"/>
      <path d="M70 310 C 240 305 380 260 470 190 C 390 270 270 300 150 310 Z" fill="var(--sky)"/>
    </svg>
    <div class="corner-tab"></div>

    <header class="holder">
      <h1 class="holder-name">Warren Halbeck</h1>
      <p class="holder-role">General Manager</p>
    </header>

    <p class="wordmark-small">
      <span class="name">TOVRIN</span>
      <span class="descriptor">Road Construction</span>
    </p>

    <address class="address" style="font-style:normal">
      87 Marrow Ave,<br>Pendlebay, QLD, 4023
    </address>

    <ul class="contacts">
      <li>
        <svg viewBox="0 0 16 16"><circle cx="8" cy="8" r="8" fill="var(--sky)"/><path d="M5 4.5c0 4 2.5 6.5 6.5 6.5l.5-1.8-2-.8-.9 1c-1.3-.6-2.1-1.4-2.6-2.6l1-.9-.8-2z" fill="#fff"/></svg>
        0472 915 348
      </li>
      <li>
        <svg viewBox="0 0 16 16"><circle cx="8" cy="8" r="8" fill="var(--sky)"/><circle cx="8" cy="8" r="4.5" fill="none" stroke="#fff" stroke-width="1.2"/><path d="M3.5 8h9M8 3.5c-2 2.5-2 6.5 0 9M8 3.5c2 2.5 2 6.5 0 9" fill="none" stroke="#fff" stroke-width="1"/></svg>
        www.tovrin.com.au
      </li>
      <li>
        <svg viewBox="0 0 16 16"><circle cx="8" cy="8" r="8" fill="var(--sky)"/><rect x="4" y="5" width="8" height="6" fill="none" stroke="#fff" stroke-width="1.2"/><path d="M4 5l4 3.5L12 5" fill="none" stroke="#fff" stroke-width="1.2"/></svg>
        Warren.halbeck@tovrin.com.au
      </li>
    </ul>
  </section>

</main>
</body>
</html>
```